Nutrition business needs logo & business card design

We need a business card & logo design for a new company based in Toronto, Ontario Canada called Verdel Wellworks.

We provide nutrition service using metrics as guide to manage client's progress. Our service creates individualized nutrition and lifestyle strategies that focuses on improving Performance, Longevity and Weight Loss. I would like to see designs that use the color of green, gray, blue and white.

The final design should:

--convey a feeling of connectedness with positive transformation.

-- communicate the idea of awareness with guided effort that yields personal independence for a better and more productive life

Target Market(s)

Professionals who work in the IT/Computer/Engineering/Banking industry specifically Directors, Managers, CEO's.

Industry/Entity Type

Health And Wellness

Contact Information for Business Card

Dorvane Pike, Owner
email: DPIKE@verdelwellworks.example
tel: - 555-204-7718

Logo Text

better health through analytics or measure to manage

Font styles to use
Other font styles liked:
• Garamound

Colors
ffffff
abd037
85acd3
757575
34a7d7

Requirements
Must have
• Good contrast and decent size font - ease of readability, aesthetically nice colors
Nice to have
• image of chart or graph that conveys measurement or analytics
Should not have
• Borders, images of food,

```html
<!DOCTYPE html>
<html lang="en">
<head>
<meta charset="utf-8">
<title>Verdel Wellworks — Business Cards</title>
<link href="https://fonts.googleapis.com/css2?family=Open+Sans:wght@300;400&display=swap" rel="stylesheet">
<style>
  :root{
    --backdrop:#3f3936;
    --card:#0d0d0d;
    --card-edge:#1c1c1c;
    --blue:#1e8fe6;
    --green:#3fae1f;
    --white:#f2f2f2;
    --divider:#3a3a3a;
  }
  *{margin:0;padding:0;box-sizing:border-box}
  html,body{width:1200px;height:844px;overflow:hidden}
  body{
    background:var(--backdrop);
    font-family:"Open Sans",Arial,sans-serif;
    position:relative;
  }
  .card{
    position:absolute;
    width:520px;height:297px;
    background:var(--card);
    border:1px solid var(--card-edge);
    box-shadow:0 12px 30px rgba(0,0,0,.45);
  }
  .card--front{left:70px;top:440px}
  .card--back{left:620px;top:130px}

  .brand{
    position:absolute;
    display:flex;align-items:center;gap:22px;
  }
  .card--front .brand{left:40px;top:44px}
  .card--back .brand{left:50%;top:50%;transform:translate(-50%,-50%)}
  .brand__dot{
    width:84px;height:84px;border-radius:50%;
    background:var(--green);
    flex:none;
  }
  .brand__name{
    font-weight:300;font-size:33px;letter-spacing:-.5px;
    color:var(--blue);white-space:nowrap;
  }

  .person{
    position:absolute;right:290px;top:170px;
    text-align:right;color:var(--white);
    font-size:13.5px;line-height:17px;
  }
  .person__name{color:var(--blue);font-size:21px;line-height:26px;font-weight:400}
  .person__title{margin-bottom:12px}
  .person__address{font-size:14.5px;line-height:18px}

  .divider{
    position:absolute;left:248px;top:160px;
    width:1px;height:120px;background:var(--divider);
  }

  .contacts{
    position:absolute;left:264px;top:160px;
    list-style:none;color:var(--white);font-size:13px;
  }
  .contacts li{display:flex;align-items:center;gap:9px;height:19px}
  .contacts svg{width:11px;height:11px;fill:var(--blue);flex:none}
</style>
</head>
<body>

<section class="card card--back">
  <div class="brand">
    <span class="brand__dot"></span>
    <span class="brand__name">Verdel Wellworks</span>
  </div>
</section>

<section class="card card--front">
  <div class="brand">
    <span class="brand__dot"></span>
    <span class="brand__name">Verdel Wellworks</span>
  </div>

  <div class="person">
    <p class="person__name">Dorvane Pike</p>
    <p class="person__title">Managing Director</p>
    <p class="person__address">12345, Address Goes Here<br>Country Name, 123456</p>
  </div>

  <span class="divider"></span>

  <ul class="contacts">
    <li>
      <svg viewBox="0 0 12 12" aria-hidden="true"><path d="M2.5 1l2 2.2-1 1.3c.6 1.4 1.7 2.5 3 3.1l1.3-1 2.2 2-1.2 1.9C5.5 10 2 6.5 1.4 2.2z"/></svg>
      (055)-204-7718
    </li>
    <li>
      <svg viewBox="0 0 12 12" aria-hidden="true"><path d="M3 1h5l1 1v2H3zM1 5h10v5H9V8H3v2H1zM3.5 9h5v2h-5z"/></svg>
      555-204-7718
    </li>
    <li>
      <svg viewBox="0 0 12 12" aria-hidden="true"><path d="M1 2.5h10v1L6 7 1 3.5zM1 5l5 3.5L11 5v4.5H1z"/></svg>
      dpike@verdelwellworks.example
    </li>
    <li>
      <svg viewBox="0 0 12 12" aria-hidden="true"><circle cx="6" cy="6" r="5"/></svg>
      verdelwellworks.example
    </li>
  </ul>
</section>

</body>
</html>
```